Kestrel Facilities Business Card Design

We would now like to design business cards with the new Kestrel Facilities logo

Target Market(s)

Professional

Industry/Entity Type

Professional services

Contact Information for Business Card

Employee name, title, phone number, email address, corporate office address and logo.

Font styles to use
Sans Serif

Colors
0054AA
0677BA
7BADD7
CADEEF
E8F1F8

Requirements
Must have
• My logo
Should not have
• any other pictures or images besides my logo

```html
<!DOCTYPE html>
<html lang="en">
<head>
<meta charset="utf-8">
<title>Kestrel Facilities Business Card</title>
<link rel="stylesheet" href="https://fonts.googleapis.com/css2?family=Montserrat:wght@400;500;700&display=swap">
<style>
  :root {
    --stage: #2b2b2d;
    --brand-blue: #3476bd;
    --brand-deep: #2f6fb7;
    --logo-silver: #d4d9e6;
    --paper: #ffffff;
    --ink: #1c1c1c;
  }
  * { margin: 0; padding: 0; box-sizing: border-box; }
  html, body { width: 1200px; height: 960px; overflow: hidden; }
  body {
    background: var(--stage);
    font-family: "Montserrat", sans-serif;
    display: flex;
    flex-direction: column;
    align-items: center;
    justify-content: center;
    gap: 60px;
  }
  .card {
    position: relative;
    width: 620px;
    height: 354px;
    border-radius: 18px;
    overflow: hidden;
  }
  .card-back {
    background: var(--brand-blue);
    display: flex;
    align-items: center;
    justify-content: center;
  }
  .wordmark {
    display: flex;
    align-items: center;
    gap: 14px;
    font-weight: 700;
    letter-spacing: 1px;
    white-space: nowrap;
  }
  .wordmark-mark { width: 40px; height: 40px; flex: none; }
  .card-back .wordmark { color: var(--logo-silver); font-size: 36px; }
  .card-back .wordmark-mark { background: var(--logo-silver); }

  .card-front { background: var(--paper); }
  .swoosh { position: absolute; inset: 0; width: 100%; height: 100%; }
  .card-front .wordmark {
    position: absolute; left: 170px; top: 40px;
    color: var(--brand-deep); font-size: 26px;
  }
  .card-front .wordmark-mark { width: 30px; height: 30px; background: var(--brand-deep); }
  .identity {
    position: absolute; left: 20px; top: 112px; width: 250px; text-align: right;
  }
  .person-name { color: var(--brand-deep); font-weight: 700; font-size: 22px; letter-spacing: 0.5px; white-space: nowrap; }
  .person-title { color: var(--ink); font-size: 15px; margin-top: 4px; }
  .divider {
    position: absolute; left: 285px; top: 102px; width: 1.5px; height: 80px;
    background: var(--brand-deep);
  }
  .contacts {
    position: absolute; left: 298px; top: 102px; list-style: none;
    font-size: 12px; color: var(--ink);
  }
  .contacts li { display: flex; align-items: center; gap: 8px; height: 26px; white-space: nowrap; }
  .contacts svg { width: 13px; height: 13px; fill: var(--brand-deep); flex: none; }
  .address {
    position: absolute; left: 40px; top: 206px;
    font-size: 15px; color: var(--ink); white-space: nowrap;
  }
</style>
</head>
<body>
  <section class="card card-back">
    <div class="wordmark"><span class="wordmark-mark"></span>Kestrel Facilities</div>
  </section>

  <section class="card card-front">
    <svg class="swoosh" viewBox="0 0 620 354" preserveAspectRatio="none">
      <path d="M0,354 L0,338 Q600,332 612,16 L620,12 L620,354 Z" fill="#3476bd"/>
      <path d="M0,326 Q588,320 600,14" fill="none" stroke="#3476bd" stroke-width="4"/>
    </svg>
    <div class="wordmark"><span class="wordmark-mark"></span>Kestrel Facilities</div>
    <div class="identity">
      <div class="person-name">DARA WHITCOMBE</div>
      <div class="person-title">Co-Founder</div>
    </div>
    <div class="divider"></div>
    <ul class="contacts">
      <li><svg viewBox="0 0 24 24"><path d="M6.6 10.8a15.1 15.1 0 0 0 6.6 6.6l2.2-2.2a1 1 0 0 1 1-.25 11.4 11.4 0 0 0 3.6.57 1 1 0 0 1 1 1V20a1 1 0 0 1-1 1A17 17 0 0 1 3 4a1 1 0 0 1 1-1h3.5a1 1 0 0 1 1 1c0 1.25.2 2.45.57 3.57a1 1 0 0 1-.25 1z"/></svg>+254-301-44720</li>
      <li><svg viewBox="0 0 24 24"><path d="M2 5h20v14H2z M2 5l10 8 10-8" stroke="#fff" stroke-width="1.5"/></svg>info@kestrelfacilities.com</li>
      <li><svg viewBox="0 0 24 24"><circle cx="12" cy="12" r="10"/></svg>www.kestrelfacilities.com</li>
    </ul>
    <div class="address">1840 Harbor Lane Suite 210 Westvale 42</div>
  </section>
</body>
</html>
```